Modern card design needed for building development company

We are looking for a sharp modern new look for our business cards.
We are a New Zealand based company called TKR Ventures NZ LTD that specialises in subdividing large sections, housing and commercial buildings.
We have attached a photo of the current logo and would like to see it improved somehow as it looks a bit dated.
We are open to any colours.

Target Market(s)

Investors, Property buyers

Industry/Entity Type

Investment

Contact Information for Business Card

TKR VENTURES NZ LTD
www.tkrventuresnz.co.nz

Damon Whitcombe
Phone +64 21 938 104
Email dpwhitcombe@korumail.co.nz

Font styles to use
Serif
Sans Serif

Colors
0792cd
33a6d7
85cae6
6b449b
886aae
f04a50
ec1f27
f37122
f68d4d

Requirements
Must have
• Please try and make the logo more modern or if you have a similar one we would like to see it.

```html
<!DOCTYPE html>
<html lang="en">
<head>
<meta charset="utf-8">
<title>TKR Ventures NZ LTD – Business Card</title>
<link rel="stylesheet" href="https://fonts.googleapis.com/css2?family=Jost:wght@400;500&family=Oswald:wght@600&display=swap">
<style>
  :root {
    --backdrop: #2b2b2b;
    --card: #1f1f20;
    --ink: #f2f2f2;
    --ink-soft: #bdbdbd;
    --accent: #33a6d7;
    --rule: #d9d9d9;
  }
  * { margin: 0; padding: 0; box-sizing: border-box; }
  html, body {
    width: 1200px; height: 904px; overflow: hidden;
    background: var(--backdrop);
  }
  .canvas {
    position: relative; width: 1200px; height: 904px;
    font-family: "Jost", sans-serif; color: var(--ink);
  }
  .card {
    position: absolute; left: 270px; width: 660px; height: 377px;
    background: var(--card);
    box-shadow: 0 10px 30px rgba(0,0,0,.45);
  }
  .card--front { top: 55px; }
  .card--back { top: 472px; }

  /* Front */
  .brand-name {
    position: absolute; top: 150px; left: 0; right: 0;
    text-align: center; font-size: 30px; font-weight: 400;
    letter-spacing: 4px; color: var(--ink-soft);
  }
  .front-web {
    position: absolute; top: 250px; left: 0; right: 0;
    text-align: center; font-size: 16px; letter-spacing: 1.5px;
    color: var(--ink);
  }
  .web-highlight { color: var(--accent); font-weight: 500; }

  /* Back */
  .identity {
    position: absolute; top: 120px; right: 345px; text-align: right;
  }
  .person-name {
    font-family: "Oswald", sans-serif; font-weight: 600;
    font-size: 40px; line-height: 1; letter-spacing: .5px;
    color: var(--ink); text-transform: uppercase;
  }
  .person-role {
    margin-top: 4px; font-size: 25px; font-weight: 500;
    letter-spacing: 1.5px; color: var(--accent);
  }
  .divider {
    position: absolute; top: 128px; left: 332px;
    width: 2px; height: 72px; background: var(--rule);
  }
  .contacts {
    position: absolute; top: 126px; left: 350px; list-style: none;
  }
  .contacts li {
    display: flex; align-items: center; gap: 12px;
    height: 25px; font-size: 17px; letter-spacing: 1px;
  }
  .contacts svg { width: 16px; height: 16px; flex: none; }
  .address {
    position: absolute; top: 290px; left: 120px;
    display: flex; align-items: center; gap: 14px;
    font-size: 20px; letter-spacing: 2px;
  }
  .address svg { width: 16px; height: 22px; }
</style>
</head>
<body>
<main class="canvas">
  <section class="card card--front" aria-label="Card front">
    <p class="brand-name">TKR VENTURES NZ LTD</p>
    <p class="front-web">www.<span class="web-highlight">tkrventuresnz</span>.co.nz</p>
  </section>

  <section class="card card--back" aria-label="Card back">
    <div class="identity">
      <h1 class="person-name">Damon Whitcombe</h1>
      <p class="person-role">Founder/CEO</p>
    </div>
    <span class="divider"></span>
    <ul class="contacts">
      <li>
        <svg viewBox="0 0 24 24" aria-hidden="true"><path fill="#33a6d7" d="M6.6 10.8a15.1 15.1 0 0 0 6.6 6.6l2.2-2.2c.3-.3.7-.4 1-.2 1.1.4 2.3.6 3.6.6.6 0 1 .4 1 1V20c0 .6-.4 1-1 1A17 17 0 0 1 3 4c0-.6.4-1 1-1h3.5c.6 0 1 .4 1 1 0 1.3.2 2.5.6 3.6.1.3 0 .7-.2 1z"/></svg>
        <span>+64 21 938 104</span>
      </li>
      <li>
        <svg viewBox="0 0 24 24" aria-hidden="true"><rect x="2.5" y="5" width="19" height="14" rx="1" fill="none" stroke="#33a6d7" stroke-width="2"/><path d="M3 6l9 7 9-7" fill="none" stroke="#33a6d7" stroke-width="2"/></svg>
        <span>dpwhitcombe@korumail.co.nz</span>
      </li>
      <li>
        <svg viewBox="0 0 24 24" aria-hidden="true"><g fill="none" stroke="#33a6d7" stroke-width="1.8"><circle cx="12" cy="12" r="9.5"/><ellipse cx="12" cy="12" rx="4.2" ry="9.5"/><path d="M2.5 12h19M4 7h16M4 17h16"/></g></svg>
        <span>www.<span class="web-highlight">tkrventuresnz</span>.co.nz</span>
      </li>
    </ul>
    <p class="address">
      <svg viewBox="0 0 16 22" aria-hidden="true"><path fill="#33a6d7" d="M8 0a8 8 0 0 0-8 8c0 6 8 14 8 14s8-8 8-14a8 8 0 0 0-8-8zm0 11a3 3 0 1 1 0-6 3 3 0 0 1 0 6z"/></svg>
      <span>Your Street Address, New Zealand, 1234</span>
    </p>
  </section>
</main>
</body>
</html>
```